Brindovalle Business cards

Dear team, I need to get the design file to suit it to our team. The focus of the business card is the Automotive Market and the design must be in black colour and the logo must be in glossy black. On the front of the card I need to get the following info:

- Name and Surname
- Title
- eMail
- Phone Number
- Skype account
- domain address

```html
<!DOCTYPE html>
<html lang="en">
<head>
<meta charset="UTF-8">
<title>Brindovalle Business Cards</title>
<link rel="stylesheet" href="https://fonts.googleapis.com/css2?family=Montserrat:wght@700&family=Oswald:wght@600&family=Arimo:wght@400&display=swap">
<style>
  :root {
    --backdrop: #d9d8d5;
    --card-black: #18181b;
    --card-edge: #e0262f;
    --accent-red: #e52a33;
    --text-white: #f4f4f4;
    --text-soft: #d6d6d6;
    --pattern-dark: #0f0f11;
    --pattern-gloss: #3a3a3e;
  }
  * { box-sizing: border-box; margin: 0; padding: 0; }
  html, body { width: 1200px; height: 801px; overflow: hidden; }
  body {
    background: var(--backdrop);
    position: relative;
    font-family: "Arimo", Arial, sans-serif;
  }
  .card {
    position: absolute;
    top: 250px;
    width: 525px;
    height: 300px;
    background: var(--card-black);
    border-bottom: 4px solid var(--card-edge);
    box-shadow: 0 14px 30px rgba(0,0,0,0.25);
    overflow: hidden;
  }
  .card-front { left: 50px; }
  .card-back { left: 625px; }

  .brand {
    position: absolute;
    left: 70px;
    top: 62px;
    display: flex;
    align-items: center;
    gap: 12px;
  }
  .brand-dot {
    width: 26px;
    height: 26px;
    border-radius: 50%;
    background: var(--accent-red);
  }
  .brand-name {
    font-family: "Montserrat", Arial, sans-serif;
    font-weight: 700;
    font-size: 38px;
    letter-spacing: -0.5px;
    color: var(--text-white);
  }

  .person {
    position: absolute;
    left: 96px;
    top: 142px;
    text-align: right;
    width: 180px;
  }
  .person-name {
    font-family: "Oswald", Arial, sans-serif;
    font-weight: 600;
    font-size: 30px;
    line-height: 1;
    color: var(--accent-red);
    text-transform: uppercase;
    letter-spacing: 0.5px;
  }
  .person-title {
    margin-top: 4px;
    font-size: 14px;
    color: var(--text-soft);
  }

  .divider {
    position: absolute;
    left: 296px;
    top: 142px;
    width: 2px;
    height: 52px;
    background: var(--accent-red);
  }

  .contacts {
    position: absolute;
    left: 314px;
    top: 138px;
    list-style: none;
    font-size: 13.5px;
    color: var(--text-soft);
    line-height: 20px;
  }
  .contacts li { display: flex; align-items: center; gap: 7px; }
  .contacts svg { width: 11px; height: 11px; fill: var(--accent-red); flex: none; }
  .plain-dot {
    width: 10px; height: 10px; border-radius: 50%;
    border: 1.5px solid var(--accent-red); flex: none;
  }

  .address {
    position: absolute;
    left: 0;
    right: 0;
    top: 238px;
    text-align: center;
    font-size: 14px;
    color: var(--text-soft);
    letter-spacing: 0.2px;
  }

  .back-pattern {
    position: absolute;
    inset: 0;
    background: linear-gradient(135deg, var(--pattern-dark) 0%, #1c1c1f 45%, var(--pattern-gloss) 100%);
  }
</style>
</head>
<body>
  <section class="card card-front">
    <div class="brand">
      <span class="brand-dot"></span>
      <span class="brand-name">Brindovalle.com</span>
    </div>

    <div class="person">
      <div class="person-name">Marco Delleri</div>
      <div class="person-title">Director</div>
    </div>

    <div class="divider"></div>

    <ul class="contacts">
      <li>
        <svg viewBox="0 0 24 24" aria-hidden="true"><path d="M6.6 10.8a15.1 15.1 0 0 0 6.6 6.6l2.2-2.2a1 1 0 0 1 1-.25 11.4 11.4 0 0 0 3.6.57 1 1 0 0 1 1 1V20a1 1 0 0 1-1 1A17 17 0 0 1 3 4a1 1 0 0 1 1-1h3.5a1 1 0 0 1 1 1c0 1.25.2 2.45.57 3.57a1 1 0 0 1-.25 1z"/></svg>
        620-555-0183
      </li>
      <li>
        <svg viewBox="0 0 24 24" aria-hidden="true"><path d="M2 5h20v14H2z M2 5l10 8 10-8" fill="none" stroke="#e52a33" stroke-width="2.4"/></svg>
        info@brindovalle.com
      </li>
      <li>
        <span class="plain-dot"></span>
        brindovalle
      </li>
    </ul>

    <p class="address">2740 W Linden Ave, Harlow, Kansas 66012</p>
  </section>

  <section class="card card-back">
    <div class="back-pattern" role="img" aria-label="Glossy black repeating brand-symbol pattern with one red accent symbol"></div>
  </section>
</body>
</html>
```